Velvet Glow Co. Derma Roller packaging design

I need a box designed for a skin care brand called Velvet Glow Co. The box will be for our Derma Roller- a skin rejuvenation device. It will be sold online with lots of competition. I would like a modern, high end design, something that stands out and looks amazing. My logo is blush pink and black, for packaging i need no more than 3 colours, maybe gold if any other colour is used. A photo of a sample derma roller is attached below for an idea of what the product looks like, however my roller with have a clear handle with a black roller. The roller comes in a clear case, the box dimensions will need to be 16 cm long, 4 cm high, 4.5 cm wide.
ATTACHED ARE 2 SAMPLE BOXES AS AN EXAMPLE OF THE SIZE OF BOX REQUIRED!

Target Market(s)

25-50 year old women in the US

Colors
e667a6
000000
efefef

Requirements
Must have
• LOGO
• NAME OF PRODUCT- Cosmetic Derma Roller
• NEEDLE DEPTH- 0.25mm
• CAUTION- For personal use only, Do not use if allergic to metal, Do not use on open skin, wounds or active acne, sterilise roller before and after use.
Nice to have
• BENEFITS- Skin Rejuvenation, Collagen Induction Therapy, Increase product absorption, reduce acne scars and pigmentation
• FEATURES- 540 high quality titanium needles, ultra sharp needle tips, cross-line needle arrangement, ergonomic handle, anti slip grip,

```html
<!DOCTYPE html>
<html lang="en">
<head>
<meta charset="utf-8">
<title>Velvet Glow Co. – Cosmetic Derma Roller Box</title>
<link href="https://fonts.googleapis.com/css2?family=Oswald:wght@300;400;500&display=swap" rel="stylesheet">
<style>
  :root {
    --page-bg: #faf6f4;
    --foil-deep: #d98f80;
    --foil-mid: #e8aa9c;
    --foil-light: #f6d2c8;
    --foil-shadow: #c98578;
    --label-bg: #fdf8f3;
    --label-edge: #e2b3a3;
    --title-light: #f1c3b3;
    --title-dark: #d9998a;
    --ink: #1d1a1a;
  }
  * { margin: 0; padding: 0; box-sizing: border-box; }
  html, body {
    width: 1200px;
    height: 1200px;
    overflow: hidden;
    background: var(--page-bg);
  }
  .canvas {
    position: relative;
    width: 1200px;
    height: 1200px;
    background: radial-gradient(ellipse at center, #ffffff 0%, var(--page-bg) 75%);
  }
  .box-panel {
    position: absolute;
    left: 48px;
    width: 1104px;
    height: 356px;
    box-shadow: 0 6px 14px rgba(120, 80, 70, 0.35);
    overflow: hidden;
  }
  .box-panel--front { top: 182px; }
  .box-panel--back { top: 662px; }
  .foil-pattern {
    position: absolute;
    inset: 0;
    background:
      radial-gradient(circle at 18% 40%, rgba(201, 133, 120, 0.55) 0 14%, transparent 30%),
      radial-gradient(circle at 80% 30%, rgba(246, 210, 200, 0.7) 0 10%, transparent 28%),
      radial-gradient(circle at 92% 80%, rgba(246, 210, 200, 0.6) 0 8%, transparent 24%),
      radial-gradient(circle at 8% 85%, rgba(246, 210, 200, 0.55) 0 8%, transparent 22%),
      radial-gradient(circle at 50% 10%, rgba(240, 190, 178, 0.6) 0 10%, transparent 30%),
      linear-gradient(120deg, var(--foil-mid) 0%, var(--foil-deep) 35%, var(--foil-light) 60%, var(--foil-mid) 100%);
  }
  .label {
    position: absolute;
    background: var(--label-bg);
    border: 2px solid var(--label-edge);
    text-align: center;
  }
  .label--front {
    left: 386px;
    top: 40px;
    width: 332px;
    height: 280px;
  }
  .label--back {
    left: 248px;
    top: 58px;
    width: 608px;
    height: 238px;
    text-align: left;
    padding: 26px 28px 0 28px;
  }
  .brand-name {
    position: absolute;
    left: 0;
    right: 0;
    top: 88px;
    font-family: "Oswald", sans-serif;
    font-weight: 300;
    font-size: 30px;
    letter-spacing: 3px;
    color: var(--ink);
  }
  .product-title {
    font-family: "Oswald", sans-serif;
    font-weight: 400;
    font-size: 29px;
    letter-spacing: 0.5px;
    color: var(--title-light);
    line-height: 1;
  }
  .product-title__accent { color: var(--title-dark); }
  .label--front .product-title {
    position: absolute;
    left: 0;
    right: 0;
    top: 222px;
  }
  .label--back .product-title {
    text-align: center;
    margin-bottom: 18px;
  }
  .spec-block {
    font-family: "Oswald", sans-serif;
    font-weight: 400;
    font-size: 13.5px;
    line-height: 18.5px;
    color: var(--ink);
    text-transform: uppercase;
    margin-bottom: 18px;
  }
</style>
</head>
<body>
  <main class="canvas">
    <section class="box-panel box-panel--front">
      <div class="foil-pattern" role="img" aria-label="Rose gold foil background with tropical monstera and palm leaf pattern"></div>
      <div class="label label--front">
        <div class="brand-name">Velvet Glow Co.</div>
        <h1 class="product-title">COSMETIC DERMA <span class="product-title__accent">ROLLER</span></h1>
      </div>
    </section>

    <section class="box-panel box-panel--back">
      <div class="foil-pattern" role="img" aria-label="Rose gold foil background with tropical monstera and palm leaf pattern"></div>
      <div class="label label--back">
        <h2 class="product-title">COSMETIC DERMA <span class="product-title__accent">ROLLER</span></h2>
        <p class="spec-block">Benefits: Skin rejuvenation, collagen induction therapy, increase product absorption, reduce acne scars and pigmentation</p>
        <p class="spec-block">Features: 540 high quality 0.25 mm titanium needles, ultra sharp needle tips, cross-line needle arrangement, ergonomic handle, anti slip grip</p>
        <p class="spec-block">Caution: For personal use only, do not use if allergic to metal, do not use on open skin, wounds or active acne, sterilise roller before and after use.</p>
      </div>
    </section>
  </main>
</body>
</html>
```